Lip Balm Label Design

Design a label for a Lavender-Mint lip balm. We make high-quality natural essential oil products. Please use the old label as an example of what exists. The label should include purple. The final design should be eye-catching and distinct. The file should be in an AI file.

Here is the information that should be included on the label:
1) ingredients:Theobroma Cacao (Cocoa) Seed Butter, Theobroma grandiflorum Ultra Refined Butter, beesewax, Calendula Officinalis Flower Oil, Prunus Amygdalus Dulcis (Sweet Almond) Oil, cetyl alcohol and Tocopherol. Lavandula Angustifolia (Lavender) Oil and Mentha Piperita (Peppermint) Oil.

2) www.kelsoroothaven.com

3) Brand name and logo: K. Elso Aromatherapy (logo is attached- you can use with form)

```html
<!DOCTYPE html>
<html lang="en">
<head>
<meta charset="utf-8">
<title>K. Elso Aromatherapy – Lavender Mint Lip Balm Label</title>
<link rel="stylesheet" href="https://fonts.googleapis.com/css2?family=Pathway+Gothic+One&family=Playfair+Display:wght@400;500&family=Libre+Baskerville&display=swap">
<style>
  :root {
    --page: #ffffff;
    --label-purple: #7367e3;
    --panel-lilac: #e1defd;
    --ink-dark: #1e1b2e;
    --accent-lavender: #8a80ea;
    --title-purple: #6f64dd;
    --brand-green: #6a9a3c;
    --url-lilac: #e4e1ff;
    --sprig-purple: #a585e6;
    --sprig-green: #7e9f45;
  }
  * { margin: 0; padding: 0; box-sizing: border-box; }
  html, body {
    width: 1200px;
    height: 1000px;
    overflow: hidden;
    background: var(--page);
  }
  .canvas {
    position: relative;
    width: 1200px;
    height: 1000px;
  }
  .label {
    position: absolute;
    left: 204px;
    top: 203px;
    width: 792px;
    height: 594px;
    background: var(--label-purple);
    overflow: hidden;
  }
  .ingredients-panel {
    position: absolute;
    left: 12px;
    top: 44px;
    width: 133px;
    height: 507px;
    background: var(--panel-lilac);
    border-radius: 20px;
  }
  .ingredients-text {
    position: absolute;
    left: -241px;
    top: 238px;
    width: 640px;
    height: 116px;
    transform-origin: 50% 50%;
    transform: rotate(90deg) scaleX(0.757);
    font-family: "Pathway Gothic One", "Oswald", sans-serif;
    font-size: 23px;
    line-height: 29px;
    color: var(--ink-dark);
  }
  .ingredients-line {
    display: block;
    white-space: nowrap;
    text-align: justify;
    text-align-last: justify;
  }
  .ingredients-heading {
    color: var(--accent-lavender);
  }
  .brand-mark {
    position: absolute;
    left: 376px;
    top: 54px;
    width: 40px;
    height: 40px;
    border-radius: 50%;
    background: var(--brand-green);
  }
  .brand-name {
    position: absolute;
    left: 246px;
    top: 140px;
    width: 300px;
    text-align: center;
    font-family: "Playfair Display", serif;
    font-weight: 500;
    font-size: 38px;
    line-height: 46px;
    color: var(--brand-green);
  }
  .sprig-wreath {
    position: absolute;
    left: 210px;
    top: 331px;
    width: 373px;
    height: 246px;
    border-radius: 0 0 190px 190px;
    background: radial-gradient(ellipse at 50% 85%, var(--sprig-green) 0%, rgba(126,159,69,0.55) 35%, rgba(165,133,230,0.7) 60%, rgba(165,133,230,0) 80%);
  }
  .product-badge {
    position: absolute;
    left: 313px;
    top: 301px;
    width: 166px;
    height: 108px;
    background: #ffffff;
    border-radius: 20px;
    display: flex;
    align-items: center;
    justify-content: center;
  }
  .product-name {
    font-family: "Playfair Display", serif;
    font-weight: 400;
    font-size: 50px;
    line-height: 48px;
    color: var(--title-purple);
    text-align: center;
    transform: scaleX(0.62);
    white-space: nowrap;
    letter-spacing: -1px;
  }
  .website {
    position: absolute;
    left: 749px;
    top: 118px;
    height: 370px;
    writing-mode: vertical-rl;
    font-family: "Libre Baskerville", serif;
    font-size: 23px;
    color: var(--url-lilac);
    white-space: nowrap;
  }
</style>
</head>
<body>
<div class="canvas">
  <section class="label">
    <aside class="ingredients-panel"></aside>
    <p class="ingredients-text">
      <span class="ingredients-line"><span class="ingredients-heading">INGREDIENTS:</span> Theobroma Cacao (Cocoa) Seed Butter, Theobroma</span>
      <span class="ingredients-line">grandiflorum Ultra Refined Butter, beesewax, Calendula Officinalis Flower Oil,</span>
      <span class="ingredients-line">Prunus Amygdalus Dulcis (Sweet Almond) Oil, cetyl alcohol and Tocopherol.</span>
      <span class="ingredients-line">Lavandula Angustifolia (Lavender) Oil and Mentha Piperita (Peppermint) Oil.</span>
    </p>

    <div class="brand-mark" aria-hidden="true"></div>
    <h1 class="brand-name">K. Elso<br>Aromatherapy</h1>

    <div class="sprig-wreath" role="img" aria-label="Illustrated wreath of lavender sprigs and green leaves"></div>

    <div class="product-badge">
      <h2 class="product-name">LAVENDER<br>MINT</h2>
    </div>

    <p class="website">www.kelsoroothaven.com</p>
  </section>
</div>
</body>
</html>
```